Website Redesign using existing images, copy etc.

I'm looking for a website redesign/refresh of my current WordPress website. I would like to utilize the same photography, a new photo viewer, and an overall refresh of the entire design. This will need to be WordPress with simple accessibility to make changes as we add additional properties and make updates. We auction luxury real estate and luxury yachts for non-distressed sellers. It needs to be simple, luxurious and with ease of use for both web and especially mobile. www.BrindleHarrow.com

```html
<!DOCTYPE html>
<html lang="en">
<head>
<meta charset="utf-8">
<title>Brindle Harrow — Luxury Real Estate &amp; Yacht Auctions</title>
<link href="https://fonts.googleapis.com/css2?family=Gilda+Display&family=Montserrat:wght@400;500;600&family=Pinyon+Script&display=swap" rel="stylesheet">
<style>
:root{
  --gold:#a8916a;
  --ink:#1f1f1f;
  --text:#4a4a4a;
  --muted:#8a8a8a;
  --paper:#ffffff;
  --sand:#efebe4;
  --mist:#f3f3f3;
  --night:#161616;
  --line:#d9d4cb;
}
*{box-sizing:border-box;margin:0;padding:0}
html,body{width:1200px;height:5076px;overflow:hidden}
body{background:var(--paper);color:var(--text);font-family:"Montserrat",Arial,sans-serif;position:relative}
.abs{position:absolute}
.eyebrow{font-size:12px;letter-spacing:4px;text-transform:uppercase;color:var(--muted);font-weight:500}
.btn{display:inline-block;background:var(--gold);color:#fff;font-size:12px;letter-spacing:2.5px;text-transform:uppercase;font-weight:600;padding:0 26px;height:44px;line-height:44px}

/* hero */
.hero{position:absolute;left:0;top:0;width:1200px;height:712px;overflow:hidden}
.hero .photo{position:absolute;inset:0;background:
  radial-gradient(ellipse 260px 120px at 860px 520px,rgba(255,214,150,.55),transparent 70%),
  radial-gradient(ellipse 200px 90px at 520px 470px,rgba(255,220,160,.45),transparent 70%),
  radial-gradient(ellipse 300px 160px at 1080px 300px,rgba(230,220,200,.45),transparent 70%),
  radial-gradient(ellipse 420px 140px at 600px 690px,rgba(40,70,40,.9),transparent 70%),
  linear-gradient(180deg,#1a2838 0%,#34495a 30%,#8a8674 55%,#5e6450 75%,#25331f 100%)}
.hero .shade{position:absolute;inset:0;background:linear-gradient(90deg,rgba(10,15,25,.6),rgba(10,15,25,.05) 70%)}
.nav{position:absolute;left:88px;top:30px;width:1024px;height:40px;display:flex;align-items:center;color:#fff}
.logo{font-family:"Gilda Display",Georgia,serif;font-size:24px;letter-spacing:4px;text-transform:uppercase;color:#fff}
.nav ul{list-style:none;display:flex;gap:34px;margin-left:62px;font-size:12px;letter-spacing:2px;font-weight:600}
.nav .phone{margin-left:auto;font-size:14px;font-weight:600;display:flex;align-items:center;gap:8px}
.nav .grid{margin-left:26px}
.hero-copy{position:absolute;left:88px;top:246px;color:#fff}
.hero-copy .eyebrow{color:#fff}
.hero-copy h1{font-family:"Gilda Display",Georgia,serif;font-weight:400;font-size:52px;line-height:60px;margin-top:14px}
.hero-copy .btns{margin-top:30px;display:flex;gap:18px}
.hero-copy .btn{font-size:11px;height:40px;line-height:40px;padding:0 22px}

/* intro */
.intro-photo{left:88px;top:800px;width:564px;height:392px;border-radius:0 0 0 40px;box-shadow:0 10px 30px rgba(0,0,0,.12);background:
  radial-gradient(ellipse 200px 70px at 300px 210px,rgba(255,255,255,.95),rgba(230,236,242,.6) 55%,transparent 75%),
  radial-gradient(ellipse 260px 60px at 260px 290px,rgba(255,255,255,.7),transparent 70%),
  linear-gradient(165deg,#6e9fcf 0%,#3274b2 40%,#1d5e98 70%,#17507f 100%)}
.intro{left:688px;top:826px;width:440px}
.intro h2{font-family:"Gilda Display",Georgia,serif;font-weight:400;font-size:54px;line-height:58px;color:var(--ink);margin-top:10px}
.intro p{font-size:12px;line-height:20px;margin-top:18px}
.intro .btn{margin-top:22px}

/* upcoming */
.sec-title{left:0;width:1200px;text-align:center}
.sec-title h2{font-family:"Gilda Display",Georgia,serif;font-weight:400;font-size:50px;color:var(--ink);margin-top:6px}
.cards{left:0;top:1412px;width:1200px;height:588px;display:flex}
.card{width:300px;height:588px;position:relative;color:#fff;border-left:1px solid rgba(255,255,255,.3)}
.card::after{content:"";position:absolute;left:0;right:0;top:0;height:110px;background:linear-gradient(180deg,rgba(0,0,0,.45),transparent)}
.card .meta{position:absolute;left:16px;top:20px;font-size:13px;line-height:20px;z-index:1}
.card .meta b{display:block;font-weight:500;opacity:.8}
.card .vert{position:absolute;left:12px;bottom:40px;writing-mode:vertical-rl;transform:rotate(180deg);font-size:12px;letter-spacing:1px}
.c1{background:radial-gradient(ellipse 160px 90px at 150px 260px,rgba(220,225,215,.7),transparent 70%),linear-gradient(180deg,#3f4d42,#7e927a 45%,#4f6a3e 70%,#27301f)}
.c2{background:radial-gradient(ellipse 150px 100px at 170px 300px,rgba(210,205,190,.6),transparent 70%),linear-gradient(180deg,#36434f,#6f7f86 45%,#4a5848 70%,#1f2628)}
.c3{background:radial-gradient(ellipse 90px 160px at 150px 320px,rgba(230,220,200,.6),transparent 70%),linear-gradient(180deg,#2c4a20,#5f7f34 45%,#3e5a26 70%,#8a7a5c)}
.c4{background:radial-gradient(ellipse 160px 120px at 150px 330px,rgba(240,200,200,.55),transparent 70%),linear-gradient(180deg,#5b4f7a,#a98aa6 45%,#7c5f7e 70%,#2f2840)}

/* featured */
.featured{left:0;top:2152px;width:1200px;height:432px;background:var(--sand)}
.featured h2{position:absolute;left:80px;top:96px;font-family:"Gilda Display",Georgia,serif;font-weight:400;font-size:48px;color:var(--ink)}
.featured p{position:absolute;left:80px;top:172px;width:560px;font-size:13px;line-height:22px}
.featured .btn{position:absolute;left:80px;top:290px}
.press{position:absolute;left:720px;top:76px;display:grid;grid-template-columns:repeat(3,140px);gap:12px 14px}
.press span{height:86px;border:1px solid var(--line);background:#f7f5f1;display:flex;align-items:center;justify-content:center;text-align:center;font-family:"Gilda Display",Georgia,serif;font-size:16px;color:#2a2a2a;padding:0 10px}

/* about */
.portrait{left:88px;top:2688px;width:416px;height:452px;border-radius:0 40px 0 0;background:
  radial-gradient(ellipse 140px 200px at 210px 440px,#25324a,transparent 75%),
  radial-gradient(ellipse 120px 90px at 80px 80px,rgba(110,150,100,.6),transparent 70%),
  linear-gradient(180deg,#cfd5da,#a3adb5 50%,#3a4456 85%,#222b3b)}
.signature{left:96px;top:3156px;font-family:"Pinyon Script",cursive;font-size:34px;color:var(--ink)}
.sig-role{left:210px;top:3210px;font-size:11px;color:var(--muted)}
.about{left:580px;top:2736px;width:520px}
.about h2{font-family:"Gilda Display",Georgia,serif;font-weight:400;font-size:52px;color:var(--ink);margin-top:6px}
.about p{font-size:13px;line-height:22px;margin-top:14px}
.about .btn{margin-top:22px}

/* sold by */
.sold{left:0;top:3304px;width:1200px;height:700px;background:var(--mist)}
.sold .head{position:absolute;top:44px;left:0;width:1200px;text-align:center}
.sold h2{font-family:"Gilda Display",Georgia,serif;font-weight:400;font-size:50px;color:var(--ink);margin-top:4px}
.sold .lead{position:absolute;top:128px;left:180px;width:840px;text-align:center;font-size:13px;line-height:22px}
.strip{position:absolute;top:268px;left:0;width:1200px;height:332px}
.strip div{position:absolute;top:0;height:332px}
.s1{left:0;width:100px;background:linear-gradient(180deg,#9fb7c8,#6f8a6a 50%,#4f6e4f)}
.s2{left:114px;width:180px;background:linear-gradient(180deg,#7fb0d8,#a5c7de 35%,#5b8a56 65%,#cfc6b2)}
.s3{left:308px;width:130px;background:linear-gradient(180deg,#a7c3d6,#dfe4e6 50%,#e9e3d6)}
.s5{left:762px;width:170px;background:linear-gradient(180deg,#8fbde0,#b7d3e6 35%,#5d8f4a 60%,#d8cfbf)}
.s6{left:946px;width:150px;background:linear-gradient(180deg,#d3bc9a,#a88a66 50%,#7a5e40)}
.s7{left:1110px;width:90px;background:linear-gradient(180deg,#1f2f4a,#4b5466 45%,#c4904a)}
.hero-card{position:absolute;left:452px;top:3528px;width:300px;height:454px;border-radius:0 0 0 24px;color:#fff;box-shadow:0 12px 30px rgba(0,0,0,.2);background:
  radial-gradient(ellipse 120px 80px at 150px 240px,rgba(90,140,70,.9),transparent 70%),
  linear-gradient(180deg,#8ab3d2,#3a6f98 35%,#2d5f86 55%,#3e6b3b 75%,#1d3d58)}
.hero-card .place{position:absolute;left:20px;bottom:64px;font-size:16px;font-weight:600}
.hero-card .story{position:absolute;left:20px;bottom:34px;font-size:10px;letter-spacing:2px;font-weight:600}
.arrow-btn{position:absolute;top:3716px;width:40px;height:40px;border-radius:50%;background:rgba(40,40,40,.55)}

/* contact */
.contact{left:0;top:4004px;width:1200px;height:556px;background:linear-gradient(180deg,#f6f6f5,#eceae6)}
.contact .head{position:absolute;top:64px;left:0;width:1200px;text-align:center}
.contact h2{font-family:"Gilda Display",Georgia,serif;font-weight:400;font-size:50px;color:var(--ink);margin-top:4px}
.form{position:absolute;left:180px;top:176px;width:840px}
.row{display:flex;gap:12px;margin-bottom:14px}
.field{flex:1;height:52px;background:#fff;border:1px solid var(--line);font-size:12px;color:#555;padding:0 14px;display:flex;align-items:center}
.field.select{justify-content:space-between}
.field.area{height:140px;align-items:flex-start;padding-top:14px}
.form .submit{display:block;width:200px;margin:20px auto 0;text-align:center}

/* footer */
.footer{left:0;top:4560px;width:1200px;height:516px;background:var(--night);color:#fff}
.footer .logo{position:absolute;left:88px;top:90px;font-size:26px}
.footer ul{position:absolute;left:88px;top:192px;list-style:none;display:flex;gap:30px;font-size:13px;letter-spacing:1.5px;font-weight:500}
.badge{position:absolute;left:88px;top:264px;width:64px;height:64px;border-radius:50%;border:2px solid #c8c8c8}
.socials{position:absolute;left:176px;top:280px;display:flex;gap:14px}
.socials span{width:34px;height:34px;border-radius:50%;border:1.5px solid #ddd}
.alerts{position:absolute;left:780px;top:96px;width:330px}
.alerts .eyebrow{color:#ddd;font-size:11px}
.alerts .in{margin-top:22px;height:48px;background:#fff;color:#555;font-size:13px;display:flex;align-items:center;padding:0 16px;gap:10px}
.alerts .in+.in{margin-top:10px}
.alerts .btn{margin-top:14px}
.footer .rule{position:absolute;left:88px;right:88px;top:428px;border-top:1px solid #333}
.footer .copy{position:absolute;left:88px;top:460px;font-size:12px;color:#999}
.footer .copy b{color:var(--gold);font-weight:500}
.footer .stamp{position:absolute;right:88px;top:460px;font-size:12px;color:#999}
</style>
</head>
<body>

<header class="hero">
  <div class="photo" role="img" aria-label="Luxury waterfront estate with balconies and palm trees at dusk"></div>
  <div class="shade"></div>
  <nav class="nav">
    <span class="logo">Brindle Harrow</span>
    <ul><li>BUY</li><li>SELL</li><li>ABOUT</li><li>CONTACT</li></ul>
    <span class="phone"><svg width="14" height="14" viewBox="0 0 24 24" fill="#fff"><path d="M6.6 10.8a15 15 0 0 0 6.6 6.6l2.2-2.2c.3-.3.7-.4 1-.2 1.1.4 2.3.6 3.6.6.6 0 1 .4 1 1V20c0 .6-.4 1-1 1A17 17 0 0 1 3 4c0-.6.4-1 1-1h3.5c.6 0 1 .4 1 1 0 1.3.2 2.5.6 3.6.1.3 0 .7-.2 1z"/></svg>800-555-0147</span>
    <svg class="grid" width="22" height="22" viewBox="0 0 22 22" fill="#fff"><circle cx="3" cy="3" r="2.4"/><circle cx="11" cy="3" r="2.4"/><circle cx="19" cy="3" r="2.4"/><circle cx="3" cy="11" r="2.4"/><circle cx="11" cy="11" r="2.4"/><circle cx="19" cy="11" r="2.4"/><circle cx="3" cy="19" r="2.4"/><circle cx="11" cy="19" r="2.4"/><circle cx="19" cy="19" r="2.4"/></svg>
  </nav>
  <div class="hero-copy">
    <div class="eyebrow">The experience of</div>
    <h1>Hearing the Auctioneer’s<br>Final Proclamation</h1>
    <div class="btns"><span class="btn">Browse upcoming auctions ›</span><span class="btn">Browse past successes ›</span></div>
  </div>
</header>

<section>
  <div class="abs intro-photo" role="img" aria-label="Luxury motor yacht cruising across blue water"></div>
  <div class="abs intro">
    <div class="eyebrow">Over one billion</div>
    <h2>Dollars of Auctions<br>Marketed</h2>
    <p>The experience of hearing the auctioneer’s final proclamation of “SOLD” is unparalleled. Whether it’s the initial meeting with the seller at their estate or yacht, or the triumphant raising of the paddle by the winning buyer, we relish every moment of the process and the ensuing festivities. We’re confident that you will too.</p>
    <span class="btn">Read more ›</span>
  </div>
</section>

<section>
  <div class="abs sec-title" style="top:1282px">
    <div class="eyebrow">Upcoming real estate</div>
    <h2>&amp; Yacht Auctions</h2>
  </div>
  <div class="abs cards">
    <div class="card c1" role="img" aria-label="Coastal home with lawn in Sarasota"><div class="meta"><b>01</b>Sarasota, FL | Sold</div><div class="vert">Sold At Auction</div></div>
    <div class="card c2" role="img" aria-label="Waterfront estate in Naples"><div class="meta"><b>02</b>Naples, FL | Sold &amp; Closed</div><div class="vert">Sold Before Auction</div></div>
    <div class="card c3" role="img" aria-label="Historic Charleston house framed by greenery"><div class="meta"><b>03</b>Charleston, SC | Under Contract</div></div>
    <div class="card c4" role="img" aria-label="Grand Sarasota mansion at twilight"><div class="meta"><b>04</b>Sarasota, FL | Sold &amp; Closed</div></div>
  </div>
  <div class="abs" style="left:508px;top:2048px"><span class="btn">View all ›</span></div>
</section>

<section class="abs featured">
  <h2>As Featured In</h2>
  <p>By offering top-tier properties and vessels globally, along with strategic auction dates, exceptional marketing tactics, and a diligent public relations team, even the most prominent media outlets have taken notice. Check out some of our latest press features.</p>
  <span class="btn">View press ›</span>
  <div class="press">
    <span>The Harbor Ledger</span><span>Meridian</span><span>Coastal Review</span>
    <span>Channel Nine Business</span><span>Channel Nine News</span>
  </div>
</section>

<section>
  <div class="abs portrait" role="img" aria-label="Portrait of the founder in a navy suit"></div>
  <div class="abs signature">Miles Castellan</div>
  <div class="abs sig-role">CEO &amp; Founder</div>
  <div class="abs about">
    <div class="eyebrow">About</div>
    <h2>Brindle Harrow</h2>
    <p>Have you ever experienced a sense of purpose in your life? I consider myself fortunate enough to have felt it not once, but twice. At the age of 18, I realized my first calling as a Paratrooper in the US Army. Although I enjoyed being a Paratrooper, I knew it couldn’t last forever. After completing my service, I ventured into the advertising industry. Although it was a good experience, I always wondered if there was a second calling for me.</p>
    <p>And that’s when it happened – I discovered my true passion for Real Estate and Yacht Auctions. It was as if I was born for it.</p>
    <span class="btn">Read more ›</span>
  </div>
</section>

<section class="abs sold">
  <div class="head"><div class="eyebrow">Sold by</div><h2>Brindle Harrow</h2></div>
  <p class="lead">Brindle Harrow is a top-tier destination for luxury property auctions, having overseen the auction marketing of numerous high-end estates and yachts. Our team of luxury home auction experts is committed to helping property owners obtain the best value for their assets while ensuring a timely sale.</p>
  <div class="strip">
    <div class="s1" role="img" aria-label="Aerial view of a coastal estate"></div>
    <div class="s2" role="img" aria-label="Pool terrace with palm trees"></div>
    <div class="s3" role="img" aria-label="Bright white interior"></div>
    <div class="s5" role="img" aria-label="Lawn and palms by the water"></div>
    <div class="s6" role="img" aria-label="Warm lit living room"></div>
    <div class="s7" role="img" aria-label="Estate at night"></div>
  </div>
</section>
<div class="hero-card" role="img" aria-label="Aerial view of a peninsula estate in Grasonville, Maryland">
  <div class="place">Grasonville | Maryland</div>
  <div class="story">SUCCESS STORY ›</div>
</div>
<div class="arrow-btn" style="left:1070px"><svg width="40" height="40" viewBox="0 0 40 40"><path d="M17 13l7 7-7 7" fill="none" stroke="#fff" stroke-width="2"/></svg></div>

<section class="abs contact">
  <div class="head"><div class="eyebrow">Contact operations</div><h2>Get In Touch</h2></div>
  <div class="form">
    <div class="row"><div class="field">Name</div><div class="field">Phone</div></div>
    <div class="row"><div class="field">Email</div><div class="field select">Which Best Describes You?<svg width="10" height="6" viewBox="0 0 10 6"><path d="M0 0h10L5 6z" fill="#555"/></svg></div></div>
    <div class="row"><div class="field area">Message</div></div>
    <span class="btn submit">Submit now ›</span>
  </div>
</section>

<footer class="abs footer">
  <div class="logo">Brindle Harrow</div>
  <ul><li>HOME</li><li>BUY</li><li>SELL</li><li>ABOUT</li><li>BLOG</li><li>CONTACT</li></ul>
  <div class="badge"></div>
  <div class="socials"><span></span><span></span><span></span><span></span><span></span></div>
  <div class="alerts">
    <div class="eyebrow">Sign up for Brindle alerts</div>
    <div class="in"><svg width="14" height="14" viewBox="0 0 24 24" fill="#777"><circle cx="12" cy="8" r="5"/><path d="M3 22a9 9 0 0 1 18 0z"/></svg>Name</div>
    <div class="in"><svg width="14" height="14" viewBox="0 0 24 24" fill="none" stroke="#777" stroke-width="2"><rect x="2" y="5" width="20" height="14"/><path d="M2 5l10 8 10-8"/></svg>Email</div>
    <span class="btn">Submit ›</span>
  </div>
  <div class="rule"></div>
  <div class="copy">© 2023 <b>Brindle Harrow</b>. All rights reserved.</div>
  <div class="stamp">August 24, 2023. Layout A</div>
</footer>

</body>
</html>
```